Business Card Design

New business card design

Target Market(s)

Residential & Commercial Property Managers

Industry/Entity Type

Plumbing Services

Contact Information for Business Card

Name - Rowan Keddle, title - Director, Phone Number - 0431 286 517, email - rowan@tbk-plumbing.com.au, Company ABN - 73 215 904 386,

Font styles to use
Sans Serif

Colors
0054AA
0677BA
7BADD7
CADEEF
E8F1F8

```html
<!DOCTYPE html>
<html lang="en">
<head>
<meta charset="utf-8">
<title>TBK Plumbing Services – Business Card</title>
<link rel="stylesheet" href="https://fonts.googleapis.com/css2?family=Montserrat:wght@300;400;500;700&display=swap">
<style>
  :root {
    --ink: #1d232d;
    --navy: #1c222c;
    --sky: #2aa3df;
    --blue-deep: #0054aa;
    --blue-mid: #0677ba;
    --blue-soft: #7badd7;
    --blue-pale: #cadeef;
    --blue-mist: #e8f1f8;
    --paper: #ffffff;
    --stage: #eceef1;
    --back-mark: #3a68a6;
  }
  * { box-sizing: border-box; margin: 0; padding: 0; }
  html, body { width: 900px; height: 1200px; overflow: hidden; }
  body {
    background: var(--stage);
    font-family: "Montserrat", Arial, sans-serif;
    color: var(--ink);
    position: relative;
  }
  .card {
    position: absolute;
    width: 742px;
    height: 440px;
    border-radius: 22px;
    overflow: hidden;
  }
  .card--front { left: 80px; top: 131px; background: var(--paper); }
  .card--back { left: 79px; top: 638px; background: var(--navy); }

  .front__halo {
    position: absolute;
    left: 492px; top: 120px;
    width: 250px; height: 250px;
    border-radius: 50%;
    background: var(--blue-mist);
  }
  .brand { position: absolute; color: var(--ink); font-weight: 300; }
  .brand__name {
    display: block;
    font-size: 104px;
    line-height: 1;
    letter-spacing: 2px;
  }
  .brand__tagline {
    display: block;
    font-size: 14px;
    letter-spacing: 10.5px;
    line-height: 1;
  }
  .card--front .brand { left: 38px; top: 8px; }
  .card--front .brand__tagline { margin: 12px 0 0 20px; }

  .person { position: absolute; left: 37px; top: 175px; }
  .person__name { font-size: 26px; font-weight: 700; line-height: 1.1; }
  .person__title { font-size: 15px; font-weight: 500; margin-top: 3px; }

  .address {
    position: absolute; left: 38px; top: 254px;
    font-style: normal; font-size: 16.5px; line-height: 20px;
  }

  .contacts { position: absolute; left: 40px; top: 320px; list-style: none; }
  .contacts li {
    display: flex; align-items: center;
    height: 30.5px;
    font-size: 16px;
  }
  .contacts svg { width: 17px; height: 17px; margin-right: 10px; fill: var(--ink); }

  .front__band {
    position: absolute; left: 0; bottom: 0;
    width: 480px; height: 21px;
    background: var(--ink);
  }
  .front__abn {
    position: absolute; right: 0; bottom: 0;
    width: 282px; height: 40px;
    background: var(--sky);
    clip-path: polygon(40px 0, 100% 0, 100% 100%, 0 100%);
    border-left: 0;
    display: flex; align-items: center; justify-content: flex-end;
    padding-right: 36px;
    font-size: 15px; color: var(--ink);
  }
  .front__abn::before {
    content: "";
    position: absolute; left: -8px; bottom: 0;
  }
  .front__abn strong { font-weight: 700; margin-right: 5px; }
  .front__gap {
    position: absolute; left: 455px; bottom: 0;
    width: 14px; height: 21px;
    background: var(--paper);
    transform: skewX(-45deg);
  }

  .card--back .brand {
    color: var(--back-mark);
    left: 0; right: 0; top: 148px;
    text-align: center;
  }
  .card--back .brand__name { font-size: 128px; letter-spacing: 4px; }
  .card--back .brand__tagline { font-size: 16px; letter-spacing: 16px; margin-top: 36px; padding-left: 16px; }
</style>
</head>
<body>

<section class="card card--front" aria-label="Business card front">
  <div class="front__halo"></div>

  <div class="brand">
    <span class="brand__name">tbk</span>
    <span class="brand__tagline">plumbing services</span>
  </div>

  <div class="person">
    <h1 class="person__name">Rowan Keddle</h1>
    <p class="person__title">Director</p>
  </div>

  <address class="address">42 Harbour Ridge Road<br>Bayview, QLD 4207</address>

  <ul class="contacts">
    <li>
      <svg viewBox="0 0 24 24" aria-hidden="true"><path d="M6.6 10.8a15.1 15.1 0 0 0 6.6 6.6l2.2-2.2c.3-.3.7-.4 1-.2 1.1.4 2.3.6 3.6.6.6 0 1 .4 1 1V20c0 .6-.4 1-1 1A17 17 0 0 1 3 4c0-.6.4-1 1-1h3.5c.6 0 1 .4 1 1 0 1.3.2 2.5.6 3.6.1.3 0 .7-.2 1z"/></svg>
      0431 286 517
    </li>
    <li>
      <svg viewBox="0 0 24 24" aria-hidden="true"><path d="M3 6h18v12H3z M3 6l9 7 9-7" fill="none" stroke="#1d232d" stroke-width="0"/><path d="M3 7.5 12 13l9-5.5V18H3z"/><path d="M3 5.5h18L12 11z"/></svg>
      rowan@tbk-plumbing.com.au
    </li>
    <li>
      <svg viewBox="0 0 24 24" aria-hidden="true"><circle cx="12" cy="12" r="9"/><path d="M8 7c2 0 3 1 2.5 2.5S8 11 8.5 13s2 2 1.5 4M15 6c-1 1.5 0 2.5 1.5 3s2 2 1 3.5" fill="none" stroke="#fff" stroke-width="1.6"/></svg>
      www.tbk-plumbing.com.au
    </li>
  </ul>

  <div class="front__band"></div>
  <div class="front__abn"><strong>ABN</strong> - 73 215 904 386</div>
</section>

<section class="card card--back" aria-label="Business card back">
  <div class="brand">
    <span class="brand__name">tbk</span>
    <span class="brand__tagline">plumbing services</span>
  </div>
</section>

</body>
</html>
```